Luxury travel agency needs a website design

We are a travel agency specializing in booking luxury vacations. We specialize in Hawaii, Europe and Caribbean, but will do all vacations. I want a very classy website design which would attract luxury clients. The company name is "Harbors and Hammocks Travel Agency". Would love the web design to go with the color scheme of the logo. Hex codes included in files. Logo is attached. Would also love more Grey in the website. I want it very elegant

Coding

Coded - Design and coding required

Font styles to use
Sans Serif
Decorative

Requirements
Must have
• - Consultation Tab or a page where the client can fill out a short form about what vacation that they would want to book. I want this info to be sent to me in order for me to contact them.
- Somewhere with my contact info "email: marla@harborsandhammockstravel.example and phone number"
- Social media links
- About section "Marla Dunbevy - Agency Owner (picture provided)
Marla has been traveling full time for the passed two years and has been very passionate about travel from a young age. Marla is dedicated to working closely with clients to book their dream vacation.
Marla's specializations include honeymoons and anniversaries focusing on travel in Europe, Hawaii and all inclusive resorts in the Caribbean.

```html
<!DOCTYPE html>
<html lang="en">
<head>
<meta charset="utf-8">
<title>Harbors and Hammocks Travel Agency</title>
<link href="https://fonts.googleapis.com/css2?family=Montserrat:wght@400;500;600;700&family=Rye&display=swap" rel="stylesheet">
<style>
:root{
  --orange:#f0915a;
  --orange-soft:#f6c3a3;
  --ink:#222222;
  --grey-text:#4a4a4a;
  --page:#f7f7f7;
  --card:#ffffff;
  --night:#121212;
  --white:#ffffff;
}
*{box-sizing:border-box;margin:0;padding:0}
html,body{width:1200px;height:4777px;overflow:hidden}
body{position:relative;background:var(--page);font-family:"Montserrat",Arial,sans-serif;color:var(--ink)}
.abs{position:absolute}
.deco{font-family:"Rye",Georgia,serif;font-weight:400}
.btn{position:absolute;display:flex;align-items:center;justify-content:center;background:var(--orange);color:var(--white);border-radius:30px;font-weight:600;text-transform:uppercase;letter-spacing:.5px}
.photo{position:absolute;border-radius:14px}

/* top bar */
.topbar{left:0;top:0;width:1200px;height:41px;background:var(--orange);color:var(--white);font-size:13px}
.topbar .mail{position:absolute;left:172px;top:12px;display:flex;align-items:center;gap:8px}
.topbar .phone{position:absolute;left:730px;top:12px;display:flex;align-items:center;gap:8px}
.topbar .social{position:absolute;left:880px;top:11px;display:flex;gap:12px}
.topbar .social span{width:19px;height:19px;border-radius:50%;background:var(--white)}

/* hero */
.hero{left:0;top:41px;width:1200px;height:800px;border-radius:0 0 55% 55% / 0 0 95px 95px;
  background:linear-gradient(180deg,#e9a58f 0%,#d79a92 22%,#6d7e8e 48%,#3a5f70 62%,#2d3b35 78%,#8e1f2d 100%)}
.brand{position:absolute;color:var(--ink);font-weight:700;text-transform:uppercase;line-height:1.15}
.brand-hero{left:172px;top:100px;font-size:19px;color:var(--ink)}
.brand-hero small{display:block;font-size:19px}
.brand-dot{position:absolute;left:205px;top:60px;width:34px;height:34px;border-radius:50%;background:var(--orange)}
.nav{position:absolute;top:110px;font-size:16px;font-weight:500;color:var(--ink);text-transform:uppercase}
.hero-title{right:174px;top:240px;text-align:right;color:var(--white);font-size:50px;line-height:76px}

/* section headings */
.heading{font-size:38px;color:var(--ink)}
.heading em{font-style:normal;color:var(--orange)}
.para{font-size:12.5px;line-height:26px;color:var(--grey-text)}

/* reviews */
.review{position:absolute;top:2287px;width:308px;height:195px;background:var(--card);border-radius:12px;box-shadow:0 4px 18px rgba(0,0,0,.06)}
.review .avatar{position:absolute;left:18px;top:24px;width:88px;height:88px;border-radius:50%;background:linear-gradient(135deg,#c9a58e,#7a5a48)}
.review h4{position:absolute;left:120px;top:28px;font-size:16px;font-weight:500}
.review .stars{position:absolute;left:120px;top:52px;color:var(--orange);font-size:15px;letter-spacing:3px}
.review p{position:absolute;left:120px;top:88px;width:170px;font-size:11.5px;line-height:19px;color:var(--grey-text);text-align:justify}
.review .who{position:absolute;left:120px;top:155px;font-size:12px;font-weight:700}
.dot{position:absolute;top:2549px;width:18px;height:18px;border-radius:50%;background:var(--orange-soft)}

/* specialization cards */
.spec{position:absolute;background:var(--card);border-radius:14px;box-shadow:0 4px 18px rgba(0,0,0,.06);text-align:center}
.spec .img{position:absolute;left:9px;top:9px;right:9px;height:208px;border-radius:12px}
.spec h3{position:absolute;left:0;right:0;top:250px;font-size:21px;font-weight:500;text-transform:uppercase}
.spec p{position:absolute;left:20px;right:20px;top:290px;font-size:11.5px;line-height:22px;color:var(--grey-text)}
.spec .btn{left:50%;transform:translateX(-50%);top:380px;width:106px;height:50px;font-size:11px}

/* footer */
.band{left:0;top:3832px;width:1200px;height:460px;background:linear-gradient(180deg,#3e4f5f 0%,#b7795a 38%,#4b5a3f 62%,#1f2a22 100%)}
.band-title{left:0;top:3950px;width:1200px;text-align:center;color:var(--white);font-weight:700;font-size:58px;line-height:1}
.band-sub{left:0;top:4028px;width:1200px;text-align:center;color:var(--white);font-weight:700;font-size:22px;letter-spacing:8px}
.footer{left:0;top:4280px;width:1200px;height:497px;background:var(--night)}
.foot-h{position:absolute;color:var(--white);font-size:18px;font-weight:500;text-transform:uppercase;line-height:28px}
.links{position:absolute;left:571px;top:4382px;list-style:none;color:var(--white);font-size:13px;line-height:28.5px}
</style>
</head>
<body>

<header class="abs topbar">
  <div class="mail">
    <svg width="16" height="12" viewBox="0 0 16 12"><rect x="1" y="1" width="14" height="10" fill="none" stroke="#fff" stroke-width="1.4"/><path d="M1 1l7 6 7-6" fill="none" stroke="#fff" stroke-width="1.4"/></svg>
    marla@harborsandhammockstravel.example
  </div>
  <div class="phone">
    <svg width="14" height="14" viewBox="0 0 24 24"><path d="M6.6 10.8a15 15 0 006.6 6.6l2.2-2.2a1 1 0 011-.25 11.4 11.4 0 003.6.57 1 1 0 011 1V20a1 1 0 01-1 1A17 17 0 013 4a1 1 0 011-1h3.5a1 1 0 011 1 11.4 11.4 0 00.57 3.6 1 1 0 01-.25 1z" fill="#fff"/></svg>
    (555) 014-2290
  </div>
  <div class="social" aria-label="Social media links"><span></span><span></span><span></span><span></span><span></span></div>
</header>

<section class="abs hero" role="img" aria-label="Sunset over a rocky sea coast with red flowers in the foreground"></section>
<div class="brand-dot"></div>
<div class="brand brand-hero">Harbors and Hammocks<small>Travel Agency</small></div>
<nav>
  <span class="nav" style="left:554px">Home</span>
  <span class="nav" style="left:646px">About</span>
  <span class="nav" style="left:746px">Contact</span>
  <span class="btn" style="left:853px;top:93px;width:173px;height:50px;background:#3b3b3b;font-size:11.5px">Schedule a consult</span>
</nav>
<h1 class="abs deco hero-title">Harbors and Hammocks<br>Travel Agency</h1>
<a class="btn" style="left:818px;top:419px;width:208px;height:65px;font-size:16px;font-weight:500">Consult with us</a>

<!-- about -->
<h2 class="abs deco heading" style="left:172px;top:996px">About <em>Marla Dunbevy</em></h2>
<p class="abs para" style="left:172px;top:1073px;width:460px">Nemo enim ipsam voluptatem quia voluptas sit aspernatur aut odit aut fugit, sed quia consequuntur magni dolores eos qui ratione voluptatem sequi nesciunt. Neque porro quisquam est, qui dolorem ipsum quia dolor sit amet, consectetur, adipisci velit, sed quia non numquam eius modi tempora incidunt ut labore et dolore magnam aliquam quaerat voluptatem.</p>
<a class="btn" style="left:172px;top:1230px;width:125px;height:52px;font-size:13px">Read more</a>
<div class="photo" role="img" aria-label="Portrait of the agency owner" style="left:662px;top:958px;width:366px;height:366px;border-radius:44% 56% 48% 52% / 52% 44% 56% 48%;background:linear-gradient(135deg,#6b7278,#8a5a44 45%,#3ea3b8)"></div>

<!-- destinations -->
<div class="photo" role="img" aria-label="Friends posing in front of a temple at sunset" style="left:172px;top:1452px;width:428px;height:325px;background:linear-gradient(135deg,#f2b35c,#c64a3a 55%,#3d6e88)"></div>
<div class="photo" role="img" aria-label="Traveler by a colourful canal harbour" style="left:172px;top:1808px;width:199px;height:180px;background:linear-gradient(135deg,#e07b46,#c23a36 50%,#3f86a8)"></div>
<div class="photo" role="img" aria-label="Hiker on a mountain at golden hour" style="left:397px;top:1808px;width:203px;height:180px;background:linear-gradient(180deg,#e8b26e,#9b6a45 55%,#3b2e28)"></div>
<h2 class="abs deco heading" style="left:640px;top:1488px">Our <em>Destinations</em></h2>
<p class="abs para" style="left:640px;top:1560px;width:386px;text-align:justify">Nemo enim ipsam voluptatem quia voluptas sit aspernatur aut odit aut fugit, sed quia consequuntur magni dolores eos qui ratione voluptatem sequi nesciunt.</p>
<div class="photo" role="img" aria-label="Group of hikers on a mountain trail" style="left:644px;top:1679px;width:382px;height:309px;background:linear-gradient(180deg,#aab3b2,#5f7a5a 55%,#3f6b2f)"></div>

<!-- reviews -->
<h2 class="abs deco heading" style="left:0;top:2108px;width:1200px;text-align:center">Top <em>Reviews</em></h2>
<p class="abs para" style="left:280px;top:2182px;width:640px;text-align:center;font-size:13.5px;line-height:23px">Lorem ipsum dolor sit amet, consectetuer adipiscing elit. Aenean commodo ligula eget dolor. Aenean massa cum.</p>

<div class="review" style="left:-60px"><div class="avatar" role="img" aria-label="Reviewer photo"></div><h4>NAM LIBERO</h4><div class="stars">★★★★★</div><p>Aenean commodo ligula eget dolor. Aenean massa cum.</p><div class="who">- Tom Hollis</div></div>
<div class="review" style="left:278px"><div class="avatar" role="img" aria-label="Reviewer photo"></div><h4>NAM LIBERO</h4><div class="stars">★★★★★</div><p>Aenean commodo ligula eget dolor. Aenean massa cum.</p><div class="who">- Wren</div></div>
<div class="review" style="left:616px"><div class="avatar" role="img" aria-label="Reviewer photo"></div><h4>NAM LIBERO</h4><div class="stars">★★★★★</div><p>Aenean commodo ligula eget dolor. Aenean massa cum.</p><div class="who">- Isla</div></div>
<div class="review" style="left:953px"><div class="avatar" role="img" aria-label="Reviewer photo"></div><h4>NAM LIBERO</h4><div class="stars">★★★★★</div><p>Aenean commodo ligula eget dolor. Aenean massa cum.</p><div class="who">- Pemberly</div></div>
<span class="dot" style="left:560px;background:var(--orange)"></span><span class="dot" style="left:590px"></span><span class="dot" style="left:620px"></span>

<!-- specializations -->
<h2 class="abs deco heading" style="left:0;top:2662px;width:1200px;text-align:center">Marla's <em>Specializations</em></h2>

<article class="spec" style="left:172px;top:2773px;width:269px;height:460px">
  <div class="img" role="img" aria-label="Palm-lined tropical beach" style="background:linear-gradient(180deg,#9ec3dd,#4f7a55 55%,#c9a67a)"></div>
  <h3>Hawaii</h3><p>Hawaii is one of the states in the USA. Located in the Pacific Ocean, this state is composed of several islands.</p><a class="btn">Read more</a>
</article>
<article class="spec" style="left:465px;top:2773px;width:270px;height:460px">
  <div class="img" role="img" aria-label="Historic European city street at dusk" style="background:linear-gradient(180deg,#2d4d85,#4b5f7e 45%,#c4503e 75%,#2a2a33)"></div>
  <h3>Europe</h3><p>Europe is a very large and diverse continent. Europe has lots of culture and history fit for any type of person.</p><a class="btn">Read more</a>
</article>
<article class="spec" style="left:759px;top:2773px;width:268px;height:460px">
  <div class="img" role="img" aria-label="Green Caribbean island bay" style="background:linear-gradient(180deg,#4a82c4,#aac6dc 35%,#3f7a4b 65%,#2c5d3a)"></div>
  <h3>Caribbean</h3><p>These are a chain of islands located in the Caribbean Sea. Each island and country is very unique.</p><a class="btn">Read more</a>
</article>
<article class="spec" style="left:172px;top:3265px;width:412px;height:445px">
  <div class="img" role="img" aria-label="Theme park promenade with palm trees" style="background:linear-gradient(180deg,#3d7cc9,#7fa6c9 40%,#3f6b3a 70%,#8b7a68)"></div>
  <h3 style="top:240px">Starlight &amp; Cinema Parks</h3><p style="left:30px;right:30px;top:280px">Starlight and Cinema Parks are very popular theme parks for families to visit. Visiting theme parks can be very over whelming for travelers.</p><a class="btn" style="top:368px">Read more</a>
</article>
<article class="spec" style="left:616px;top:3265px;width:411px;height:445px">
  <div class="img" role="img" aria-label="Colonial Mexican town with church towers at sunset" style="background:linear-gradient(180deg,#4e6a96,#e3a46a 45%,#b5563a 75%,#6b3b2a)"></div>
  <h3 style="top:240px">Mexico</h3><p style="left:30px;right:30px;top:280px">Located in North America, Mexico is a very diverse country to visit. The popular locations in Mexico are on the coast. Mexico has pristine beaches and is tropical in nature.</p><a class="btn" style="top:368px">Read more</a>
</article>

<!-- footer -->
<section class="abs band" role="img" aria-label="Aerial view of a green island coast at sunset"></section>
<div class="abs band-title">HARBORS &amp; HAMMOCKS</div>
<div class="abs band-sub">TRAVEL AGENCY</div>
<svg class="abs" style="left:0;top:4170px" width="1200" height="120" viewBox="0 0 1200 120" aria-hidden="true">
  <path d="M0 115 Q600 -30 1200 115 L1200 120 L0 120Z" fill="#121212"/>
  <path d="M0 115 Q600 -30 1200 115" fill="none" stroke="#f0915a" stroke-width="7"/>
</svg>
<footer class="abs footer"></footer>
<div class="brand" style="left:172px;top:4440px;color:var(--white);font-size:24px;line-height:1.3">Harbors &amp; Hammocks<br>Travel Agency</div>
<h4 class="foot-h" style="left:570px;top:4336px">Quick links</h4>
<ul class="links"><li>Home</li><li>About Us</li><li>Blog</li><li>Destinations</li><li>Travel</li><li>Contact Us</li></ul>
<h4 class="foot-h" style="left:779px;top:4336px;width:260px">Subscribe to our newsletter</h4>
<p class="abs" style="left:781px;top:4408px;width:250px;color:var(--white);font-size:13px;line-height:22px">Etiam rhoncus. Maecenas temp us, tellus eget condimentum rho</p>
<div class="abs" style="left:781px;top:4472px;width:245px;height:56px;background:var(--white);border-radius:30px;padding:20px 22px;font-size:13px">Email</div>
<a class="btn" style="left:781px;top:4541px;width:124px;height:54px;font-size:12px;font-weight:500">Subscribe</a>
<div class="abs" style="left:172px;top:4668px;width:854px;height:1px;background:#777"></div>
<p class="abs" style="left:0;top:4713px;width:1200px;text-align:center;color:var(--white);font-size:13px">Copyrights @ 2021 Harbors and Hammocks. All Rights Reserved.</p>

</body>
</html>
```